TALMORK

The business want a professional looking business card. We have a scetch we will add but want the extra upgrade, and would like more suggestions for variations of our business cards.

```html
<!DOCTYPE html>
<html lang="en">
<head>
<meta charset="UTF-8">
<title>TALMORK Business Card</title>
<link href="https://fonts.googleapis.com/css2?family=Playfair+Display:wght@700&family=Lato:wght@400&display=swap" rel="stylesheet">
<style>
  :root {
    --canvas: #8e8e8e;
    --card: #1e1e1e;
    --gold: #d9a93a;
    --gold-light: #f3d36b;
    --gold-deep: #a8771c;
    --text-light: #ececec;
    --ink: #1a1a1a;
  }
  html, body {
    margin: 0;
    padding: 0;
    width: 1200px;
    height: 1200px;
    overflow: hidden;
    background: var(--canvas);
  }
  .stage {
    position: relative;
    width: 1200px;
    height: 1200px;
  }
  .card {
    position: absolute;
    left: 281px;
    width: 642px;
    height: 366px;
    border-radius: 16px;
    background: var(--card);
    overflow: hidden;
  }
  .card--front { top: 195px; }
  .card--back { top: 639px; }

  .brand {
    position: absolute;
    left: 410px;
    top: 128px;
    width: 200px;
    text-align: center;
    color: var(--gold);
  }
  .brand__name {
    font-family: "Playfair Display", serif;
    font-weight: 700;
    font-size: 27px;
    letter-spacing: 6px;
    line-height: 1;
    margin-left: 6px;
  }
  .brand__since {
    font-family: "Lato", sans-serif;
    font-size: 9.5px;
    letter-spacing: 3.5px;
    color: var(--text-light);
    margin-top: 7px;
    margin-left: 3px;
  }

  .person {
    position: absolute;
    left: 45px;
    top: 176px;
  }
  .person__name {
    font-family: "Playfair Display", serif;
    font-weight: 700;
    font-size: 28px;
    color: var(--gold);
    line-height: 1.1;
  }
  .person__role {
    font-family: "Lato", sans-serif;
    font-size: 16px;
    color: var(--text-light);
    margin-top: 2px;
  }
  .divider {
    position: absolute;
    left: 45px;
    top: 245px;
    width: 547px;
    height: 1px;
    background: linear-gradient(90deg, var(--gold-light), var(--gold));
  }
  .contact {
    position: absolute;
    left: 45px;
    top: 260px;
    font-family: "Lato", sans-serif;
    font-size: 14.5px;
    color: var(--text-light);
  }
  .contact__row {
    display: flex;
    align-items: center;
    height: 23px;
  }
  .contact__icon {
    width: 12px;
    height: 12px;
    margin-right: 11px;
    flex: none;
  }
  .footer-band {
    position: absolute;
    left: 0;
    bottom: 0;
    width: 642px;
    height: 40px;
  }
  .website {
    position: absolute;
    right: 46px;
    bottom: 7px;
    font-family: "Lato", sans-serif;
    font-size: 13.5px;
    letter-spacing: 3px;
    color: var(--ink);
  }

  .pattern-area {
    position: absolute;
    inset: 0;
    background: linear-gradient(90deg, #6a6a6a 0%, #3e3e3e 35%, #262626 60%, #121212 100%);
  }
</style>
</head>
<body>
<div class="stage">
  <section class="card card--front">
    <div class="brand">
      <div class="brand__name">TALMORK</div>
      <div class="brand__since">SINCE 2026</div>
    </div>

    <div class="person">
      <div class="person__name">Lars Henrik Østvang</div>
      <div class="person__role">CEO &amp; Founder</div>
    </div>

    <div class="divider"></div>

    <div class="contact">
      <div class="contact__row">
        <svg class="contact__icon" viewBox="0 0 24 24" aria-hidden="true">
          <path fill="#d9a93a" d="M6.6 10.8c1.4 2.8 3.8 5.1 6.6 6.6l2.2-2.2c.3-.3.7-.4 1-.2 1.1.4 2.3.6 3.6.6.6 0 1 .4 1 1V20c0 .6-.4 1-1 1C10.6 21 3 13.4 3 4c0-.6.4-1 1-1h3.5c.6 0 1 .4 1 1 0 1.3.2 2.5.6 3.6.1.3 0 .7-.2 1z"/>
        </svg>
        <span>004791234567</span>
      </div>
      <div class="contact__row">
        <svg class="contact__icon" viewBox="0 0 24 24" aria-hidden="true">
          <rect x="2" y="5" width="20" height="14" rx="1" fill="#d9a93a"/>
          <path d="M2.5 5.5 12 13l9.5-7.5" fill="none" stroke="#1e1e1e" stroke-width="1.6"/>
        </svg>
        <span>talmork.co@postmail.com</span>
      </div>
    </div>

    <svg class="footer-band" viewBox="0 0 642 40" preserveAspectRatio="none" aria-hidden="true">
      <defs>
        <linearGradient id="goldBand" x1="0" y1="0" x2="1" y2="0">
          <stop offset="0" stop-color="#f3d36b"/>
          <stop offset="0.6" stop-color="#c8952c"/>
          <stop offset="0.8" stop-color="#f5dc82"/>
          <stop offset="1" stop-color="#b8852a"/>
        </linearGradient>
      </defs>
      <path d="M0 31 H375 C395 31 390 10 412 10 H642 V40 H0 Z" fill="url(#goldBand)"/>
    </svg>
    <div class="website">www.talmork.llc</div>
  </section>

  <section class="card card--back">
    <div class="pattern-area" role="img" aria-label="Repeating embossed brand pattern fading from silver to black across the card back"></div>
  </section>
</div>
</body>
</html>
```